Website: BrightHarbor Business Consultants, Qianhai SEZ, China

Our client is a business consultancy firm and will be the first to set up in the Qianhai Shenzhen-Hong Kong Modern Service Industry Cooperation Zone, China So we need a corporate website concept that engages service, finance and technology sector companies. The company can provide all the necessary services needed to set up shop in Qianhai. They are looking for a modern, international, reliable and strong image.

Here are some websites for reference prupose:

http://www.vornelpax.com/ (we like the dynamic banner and clear, clean layout of this website)

http://www.quilbrenadvisory.com/ (we like the background city image, use of light font, hover over menu functions and color scheme - purple and grey)

http://www.dovu.com/ (we like the simplicity of this website, clear lines and we like the dynamic banner)
Updates

Hello, We are currently undecided between three logo designs.  All three have been uploaded to the design brief so that you can use them as reference for the website design. Thx

Also please take note of the addition menu selection 'About Qianhai'. Thx

Hello all Designers, First of all we want thank you for participating in our website competition, the calibre of design was high and we appreciated the expedience. Our company is Lumen Harvest Web Design and Internet Marketing based in Shenzhen, China. We anticipate rapid growth in the Chinese domestic market as the country shifts in to a service sector economy. We hope to continue building reliable working relationships with you based on idea sharing and constructive feedback. Once again, Thankyou, LH Team

Target Market(s)

International finance and technology companies looking to set up in Qianhai Special Economic Zone, China

Industry/Entity Type

Finance

Requirements
Must have
• Initial design for home page and in later selection stages a secondary page will be required.

The design should be for PSD concepts only no code!

Menu bar, Photo banner -
A. Photo banner and text overlay,
B.Photo Banner and text description to left or right.

Social Connect icons, Site search bar (top right), Logo space (top left).

Menu bar at top with Home, About Us, About Qianhai, Services, Portfolio, Partners, Our Team Contact Us.

Standard 3-4 box layout - Banner at top and 2-3 boxes under banner.

Colour scheme- A. Purple and Blue, must have light background/body
B. Shades of white, black and grey.

Simple, clear, clean, sharp.

```html
<!DOCTYPE html>
<html lang="en">
<head>
<meta charset="utf-8">
<title>BrightHarbor Business Consultants</title>
<link rel="stylesheet" href="https://fonts.googleapis.com/css2?family=Jost:wght@400&family=Tinos:ital,wght@1,700&family=Noto+Sans:wght@400&display=swap">
<style>
  :root {
    --navy: #2d2a8c;
    --blue: #1f78c1;
    --purple: #a0449c;
    --ring: #2c2a2e;
    --bg-top: #ffffff;
    --bg-mid: #d9dcf0;
    --bg-bottom: #6f80c2;
    --body-text: #4a4a55;
    --search-line: #e6e9f7;
  }
  * { margin: 0; padding: 0; box-sizing: border-box; }
  html, body { width: 1200px; height: 756px; overflow: hidden; }
  body {
    position: relative;
    background: linear-gradient(180deg, var(--bg-top) 0%, var(--bg-top) 12%, var(--bg-mid) 52%, var(--bg-bottom) 100%);
    font-family: "Noto Sans", Verdana, sans-serif;
  }
  .feature-disc { position: absolute; left: 0; top: 0; width: 1200px; height: 756px; }
  .brand {
    position: absolute; left: 80px; top: 150px;
    display: flex; align-items: center; gap: 12px;
  }
  .brand-dot { width: 26px; height: 26px; border-radius: 50%; background: var(--purple); }
  .brand-name {
    font-family: "Jost", Futura, sans-serif; font-weight: 400;
    font-size: 34px; color: var(--purple); letter-spacing: 0.5px;
  }
  .intro { position: absolute; left: 82px; top: 286px; width: 620px; }
  .intro-title {
    font-family: "Tinos", "Times New Roman", serif; font-style: italic; font-weight: 700;
    font-size: 24px; color: var(--blue); margin-bottom: 26px; white-space: nowrap;
  }
  .intro-text { font-size: 15.5px; line-height: 25px; color: var(--body-text); letter-spacing: 0.35px; }
  .intro-text span.line { display: block; white-space: nowrap; }
  .more-dots { display: inline-flex; align-items: center; gap: 3px; margin-left: 12px; vertical-align: middle; }
  .more-dots i { display: block; border-radius: 50%; background: var(--blue); }
  .more-dots i:nth-child(1) { width: 11px; height: 11px; }
  .more-dots i:nth-child(2) { width: 8px; height: 8px; }
  .more-dots i:nth-child(3) { width: 5px; height: 5px; }
  .main-nav a {
    position: absolute; display: flex; align-items: center; gap: 10px;
    font-family: "Jost", Futura, sans-serif; font-size: 19px; color: var(--navy);
    text-decoration: none; transform: translate(-100%, -50%); white-space: nowrap;
  }
  .main-nav a::after {
    content: ""; width: 18px; height: 18px; border-radius: 50%; background: var(--blue);
  }
  .main-nav a.is-active::after { background: var(--purple); }
  .social { position: absolute; left: 138px; top: 703px; display: flex; gap: 25px; }
  .social span { width: 32px; height: 32px; border-radius: 4px; }
  .social .s1 { background: var(--blue); }
  .social .s2 { background: var(--purple); }
  .social .s3 { background: #2aa6e0; }
  .site-search {
    position: absolute; left: 343px; top: 704px; width: 248px; height: 31px;
    border: 1px solid var(--search-line); display: flex; align-items: center; padding: 0 6px 0 8px;
  }
  .site-search input {
    flex: 1; min-width: 0; background: transparent; border: 0; outline: 0;
    font-family: "Noto Sans", Verdana, sans-serif; font-size: 15px; color: #fff;
  }
  .site-search input::placeholder { color: #f1f3fb; }
  .search-icon { flex-shrink: 0; width: 36px; height: 24px; }
</style>
</head>
<body>
  <svg class="feature-disc" viewBox="0 0 1200 756" role="img" aria-label="Large decorative disc filled with blue and purple circles">
    <defs>
      <radialGradient id="discFill" cx="0.35" cy="0.5" r="0.7">
        <stop offset="0" stop-color="#2a7cc4"/>
        <stop offset="0.55" stop-color="#6a5aa8"/>
        <stop offset="1" stop-color="#a4479e"/>
      </radialGradient>
    </defs>
    <ellipse cx="1344" cy="330" rx="480" ry="475" fill="var(--ring)"/>
    <ellipse cx="1350" cy="330" rx="464" ry="462" fill="url(#discFill)"/>
  </svg>

  <header>
    <div class="brand"><span class="brand-dot"></span><span class="brand-name">BrightHarbor</span></div>
    <nav class="main-nav">
      <a href="#" style="left:915px; top:74px">Home</a>
      <a href="#" style="left:889px; top:151px">About Us</a>
      <a href="#" style="left:867px; top:227px">About Qianhai</a>
      <a href="#" class="is-active" style="left:856px; top:302px">Services</a>
      <a href="#" style="left:856px; top:379px">Portfolio</a>
      <a href="#" style="left:865px; top:455px">Partners</a>
      <a href="#" style="left:893px; top:532px">Our Team</a>
      <a href="#" style="left:941px; top:607px">Contact Us</a>
    </nav>
  </header>

  <main class="intro">
    <h1 class="intro-title">Serviciae ampulum qvorat caduce altius forum on rollover</h1>
    <p class="intro-text">
      <span class="line">This text appear on rollover (hovering).&nbsp; Voluptatum deleniti atque corrupti</span>
      <span class="line">quos dolores et quas molestias excepturi sint occaecati cupiditate non</span>
      <span class="line">provident. De gustibus non disputandum. At vero eos et accusamus et iusto</span>
      <span class="line">odio dignissimos ducimus qui blanditiis praesentium&nbsp; similique sunt&nbsp; in</span>
      <span class="line">culpa qui officia deserunt mollitia animi galinae curvatum&nbsp; dici<span class="more-dots"><i></i><i></i><i></i></span></span>
    </p>
  </main>

  <footer>
    <div class="social" aria-label="Social links"><span class="s1"></span><span class="s2"></span><span class="s3"></span></div>
    <form class="site-search">
      <input type="text" placeholder="search in site">
      <svg class="search-icon" viewBox="0 0 36 24" aria-hidden="true">
        <circle cx="11" cy="10" r="7.5" fill="none" stroke="#f4f5fb" stroke-width="2.5"/>
        <line x1="17" y1="14" x2="33" y2="21" stroke="#f4f5fb" stroke-width="4" stroke-linecap="round"/>
      </svg>
    </form>
  </footer>
</body>
</html>
```